Musical download and streaming website

hello designers, I want to start up a musical website where users can download and rate music of different genres such as RnB, Hip hop, rock, afro-pop. This website should be attractive and contemporary. There will be a search column for different songs. Music files will be mp3, mwa, and others. I like blue, gold, pink and indigo colors. My website should resemble http://tunovalt.com. There should be good imaginary of music stars on my website.

```html
<!DOCTYPE html>
<html lang="en">
<head>
<meta charset="UTF-8">
<title>Velora Music</title>
<link href="https://fonts.googleapis.com/css2?family=Arimo:wght@400;700&display=swap" rel="stylesheet">
<style>
:root{
  --pink:#d8045f;
  --pink-btn:#e0086a;
  --indigo:#3b1690;
  --indigo-deep:#2a0d6e;
  --blue:#1a74db;
  --blue-light:#2f8cf0;
  --gold:#c8961a;
  --gold-dark:#a87a10;
  --white:#ffffff;
  --ink:#222222;
  --muted:#666666;
  --star:#f2b705;
}
*{margin:0;padding:0;box-sizing:border-box}
html,body{width:1200px;height:2691px;overflow:hidden}
body{font-family:"Arimo",Arial,sans-serif;color:var(--white);background:var(--white);position:relative}
a{color:inherit;text-decoration:none}

/* hero */
.hero{position:absolute;left:0;top:0;width:1200px;height:622px;
  background:linear-gradient(180deg,#3a3a3a 0%,#6a6a6a 40%,#2a2a2a 80%,#141414 100%)}
.hero-photo{position:absolute;inset:0;background:radial-gradient(ellipse at 50% 35%,rgba(200,200,200,.35),rgba(0,0,0,0) 60%)}
.brand{position:absolute;left:160px;top:50px;display:flex;align-items:center;gap:12px}
.brand-dot{width:50px;height:50px;border-radius:50%;background:var(--blue)}
.brand-name{font-size:38px;font-weight:700;color:var(--white);white-space:nowrap}
.main-nav{position:absolute;left:544px;top:64px;display:flex;gap:24px;font-size:14px;white-space:nowrap}
.main-nav a.active{color:var(--blue-light)}
.search-btn-round{position:absolute;left:1008px;top:54px;width:34px;height:34px;border-radius:50%;background:var(--pink-btn);display:flex;align-items:center;justify-content:center}
.hero-title{position:absolute;top:268px;left:0;width:1200px;text-align:center;font-size:48px;font-weight:700}
.hero-title .accent{color:var(--blue-light)}
.hero-sub{position:absolute;top:324px;left:0;width:1200px;text-align:center;font-size:14px}
.search-bar{position:absolute;left:222px;top:370px;width:756px;height:50px;background:rgba(0,0,0,.8);display:flex;align-items:center;padding:0 8px 0 16px}
.search-bar span{flex:1;font-size:11px;color:#ddd}
.search-bar .go{background:var(--gold);color:var(--white);font-size:14px;height:38px;line-height:38px;width:136px;text-align:center;white-space:nowrap}
.dots{position:absolute;left:0;width:1200px;display:flex;justify-content:center;gap:14px}
.dots i{width:9px;height:9px;border-radius:50%;background:var(--white)}
.dots i.on{background:var(--pink-btn)}

/* genres */
.genres{position:absolute;left:0;top:622px;width:1200px;height:708px;background:var(--pink)}
.section-title{position:absolute;left:0;width:1200px;text-align:center;font-size:38px;font-weight:700}
.genre-card{position:absolute;width:444px;height:249px;border:2px solid rgba(255,255,255,.8);box-shadow:0 4px 10px rgba(0,0,0,.35);
  background:linear-gradient(135deg,#111 0%,#4a4a4a 55%,#1a1a1a 100%)}
.genre-card.light{background:linear-gradient(135deg,#d8d8d8 0%,#6a6a6a 50%,#1c1c1c 100%)}
.genre-label{position:absolute;left:22px;bottom:40px;font-size:23px;font-weight:700;display:flex;align-items:center;gap:8px}
.arrow-dot{width:18px;height:18px;border-radius:50%;background:var(--blue-light);display:inline-flex;align-items:center;justify-content:center}

/* artists */
.artists{position:absolute;left:0;top:1330px;width:1200px;height:648px;background:linear-gradient(160deg,var(--indigo) 0%,#4b1587 50%,var(--indigo-deep) 100%)}
.artist-tile{position:absolute;width:210px;height:210px;border:6px solid var(--white);box-shadow:0 4px 10px rgba(0,0,0,.4)}
.artist-info{position:absolute;inset:0;display:flex;flex-direction:column;align-items:center;justify-content:center;background:rgba(0,0,0,.45)}
.artist-info h3{color:var(--pink-btn);font-size:18px}
.artist-info p{font-size:10px;margin-top:6px}
.artist-info .btn{margin-top:18px;background:var(--gold);font-size:10px;padding:7px 14px}
.slider-arrow{position:absolute}

/* songs */
.songs{position:absolute;left:0;top:1978px;width:1200px;height:552px;background:linear-gradient(180deg,var(--blue) 0%,#1666c9 100%)}
.song-card{position:absolute;width:289px;height:127px;background:#f4f4f4;box-shadow:0 3px 8px rgba(0,0,0,.3);color:var(--ink)}
.song-cover{position:absolute;left:10px;top:12px;width:104px;height:104px}
.song-time{position:absolute;left:36px;top:38px;width:52px;height:52px;border-radius:50%;background:var(--blue-light);color:var(--white);font-size:11px;display:flex;align-items:center;justify-content:center}
.song-title{position:absolute;left:124px;top:20px;width:150px;font-size:11px;font-weight:700;color:#1d1d6a;line-height:14px}
.song-rating{position:absolute;left:124px;top:58px;font-size:10px;color:var(--muted)}
.song-rating b{color:var(--star);font-weight:400;letter-spacing:1px}
.song-actions{position:absolute;left:124px;top:84px;display:flex;gap:6px;white-space:nowrap}
.song-actions span{font-size:9px;color:var(--white);padding:4px 6px}
.dl{background:var(--gold-dark)}
.rate{background:var(--pink-btn)}

/* footer */
.site-footer{position:absolute;left:0;top:2530px;width:1200px;height:161px;background:var(--white);color:var(--ink)}
.footer-brand{position:absolute;left:144px;top:48px;display:flex;align-items:center;gap:8px}
.footer-brand .brand-dot{width:44px;height:44px;background:#333}
.footer-brand .brand-name{color:#333;font-size:30px}
.footer-nav{position:absolute;left:144px;top:106px;font-size:13px;display:flex;gap:12px;white-space:nowrap}
.social{position:absolute;left:925px;top:57px;display:flex;gap:6px}
.social i{width:20px;height:20px;border-radius:50%;border:1px solid #7a8ec9}
.legal{position:absolute;left:836px;top:106px;font-size:13px;white-space:nowrap}
</style>
</head>
<body>

<header class="hero">
  <div class="hero-photo" role="img" aria-label="Black and white concert crowd with raised hands and a singer on stage"></div>
  <a class="brand" href="#"><span class="brand-dot"></span><span class="brand-name">VeloraMusic</span></a>
  <nav class="main-nav">
    <a class="active" href="#">Home</a><a href="#">About Us</a><a href="#">Artists</a><a href="#">Download Songs</a><a href="#">Contact Us</a>
  </nav>
  <a class="search-btn-round" href="#" aria-label="Search">
    <svg width="14" height="14" viewBox="0 0 14 14"><circle cx="6" cy="6" r="4" fill="none" stroke="#fff" stroke-width="2"/><line x1="9" y1="9" x2="13" y2="13" stroke="#fff" stroke-width="2"/></svg>
  </a>
  <h1 class="hero-title"><span class="accent">Velora</span> Music</h1>
  <p class="hero-sub">Search download and rate music of different genres</p>
  <div class="search-bar"><span>Search Your Artist, Songs &amp; albums</span><a class="go" href="#">Search Now !</a></div>
  <div class="dots" style="top:574px"><i class="on"></i><i></i><i></i><i></i></div>
</header>

<section class="genres">
  <h2 class="section-title" style="top:50px">Featured Genres</h2>
  <div class="genre-card" style="left:144px;top:123px" role="img" aria-label="Singer with microphone, black and white photo">
    <span class="genre-label">RnB <span class="arrow-dot"><svg width="8" height="8" viewBox="0 0 8 8"><path d="M2 1l3 3-3 3" fill="none" stroke="#fff" stroke-width="1.6"/></svg></span></span>
  </div>
  <div class="genre-card" style="left:612px;top:123px" role="img" aria-label="Rock guitarist on stage, black and white photo">
    <span class="genre-label">Rock <span class="arrow-dot"><svg width="8" height="8" viewBox="0 0 8 8"><path d="M2 1l3 3-3 3" fill="none" stroke="#fff" stroke-width="1.6"/></svg></span></span>
  </div>
  <div class="genre-card light" style="left:144px;top:396px" role="img" aria-label="Hip hop artist in hood and sunglasses, black and white photo">
    <span class="genre-label">Hip Hop <span class="arrow-dot"><svg width="8" height="8" viewBox="0 0 8 8"><path d="M2 1l3 3-3 3" fill="none" stroke="#fff" stroke-width="1.6"/></svg></span></span>
  </div>
  <div class="genre-card" style="left:612px;top:396px" role="img" aria-label="Illustrated singer with microphone, black and white">
    <span class="genre-label">Afro-Pop <span class="arrow-dot"><svg width="8" height="8" viewBox="0 0 8 8"><path d="M2 1l3 3-3 3" fill="none" stroke="#fff" stroke-width="1.6"/></svg></span></span>
  </div>
</section>

<section class="artists">
  <h2 class="section-title" style="top:52px">Top Artists</h2>
  <div class="artist-tile" style="left:144px;top:128px;background:linear-gradient(135deg,#2a1a1a,#0e0e0e)" role="img" aria-label="Male singer portrait">
    <div class="artist-info"><h3>Rowan Ellis</h3><p>USA | Top Artist 1</p><span class="btn">VIEW DETAILS</span></div>
  </div>
  <div class="artist-tile" style="left:378px;top:128px;background:linear-gradient(135deg,#3a3a3a,#0c0c0c)" role="img" aria-label="Singer in black and white"></div>
  <div class="artist-tile" style="left:610px;top:128px;background:linear-gradient(135deg,#1a1a1a,#5a5a5a 60%,#111)" role="img" aria-label="Female singer performing"></div>
  <div class="artist-tile" style="left:846px;top:128px;background:linear-gradient(135deg,#7a4a2c,#3a2418)" role="img" aria-label="Woman singing into microphone"></div>
  <div class="artist-tile" style="left:144px;top:362px;background:linear-gradient(135deg,#b8c4d2,#5a6670)" role="img" aria-label="Man singing with raised hand"></div>
  <div class="artist-tile" style="left:378px;top:362px;background:linear-gradient(135deg,#e06a1a,#5a1808)" role="img" aria-label="Singer in orange stage light"></div>
  <div class="artist-tile" style="left:610px;top:362px;background:linear-gradient(135deg,#1e1e3a,#4a3030)" role="img" aria-label="Female singer on dark stage"></div>
  <div class="artist-tile" style="left:846px;top:362px;background:linear-gradient(135deg,#6a2a8a,#1e0c3a)" role="img" aria-label="Female singer with microphone in purple light"></div>
  <svg class="slider-arrow" style="left:74px;top:334px" width="16" height="24" viewBox="0 0 16 24"><path d="M12 3L4 12l8 9" fill="none" stroke="#3d8ff5" stroke-width="3"/></svg>
  <svg class="slider-arrow" style="left:1108px;top:334px" width="16" height="24" viewBox="0 0 16 24"><path d="M4 3l8 9-8 9" fill="none" stroke="#3d8ff5" stroke-width="3"/></svg>
</section>

<section class="songs">
  <h2 class="section-title" style="top:74px">Top Songs</h2>

  <div class="song-card" style="left:144px;top:160px">
    <div class="song-cover" style="background:linear-gradient(135deg,#d0287a,#3a1a6a)" role="img" aria-label="Festival poster artwork"></div>
    <span class="song-time">2:45m</span>
    <p class="song-title">Neque porro quisquam est qui dolorem ipsum</p>
    <p class="song-rating">Ratings <b>★★★★★</b></p>
    <div class="song-actions"><span class="dl">Download Now</span><span class="rate">Rate It Now</span></div>
  </div>
  <div class="song-card" style="left:456px;top:160px">
    <div class="song-cover" style="background:linear-gradient(135deg,#e8a040,#b03a1a)" role="img" aria-label="Festival poster artwork"></div>
    <span class="song-time">2:45m</span>
    <p class="song-title">Neque porro quisquam est qui dolorem ipsum</p>
    <p class="song-rating">Ratings <b>★★★★★</b></p>
    <div class="song-actions"><span class="dl">Download Now</span><span class="rate">Rate It Now</span></div>
  </div>
  <div class="song-card" style="left:768px;top:160px">
    <div class="song-cover" style="background:linear-gradient(135deg,#1a1a1a,#b01818)" role="img" aria-label="Rock band poster artwork"></div>
    <span class="song-time">2:45m</span>
    <p class="song-title">Neque porro quisquam est qui dolorem ipsum</p>
    <p class="song-rating">Ratings <b>★★★★★</b></p>
    <div class="song-actions"><span class="dl">Download Now</span><span class="rate">Rate It Now</span></div>
  </div>
  <div class="song-card" style="left:144px;top:305px">
    <div class="song-cover" style="background:linear-gradient(135deg,#2ab0d8,#0a3a6a)" role="img" aria-label="Night club poster artwork"></div>
    <span class="song-time">2:45m</span>
    <p class="song-title">Neque porro quisquam est qui dolorem ipsum</p>
    <p class="song-rating">Ratings <b>★★★★★</b></p>
    <div class="song-actions"><span class="dl">Download Now</span><span class="rate">Rate It Now</span></div>
  </div>
  <div class="song-card" style="left:456px;top:305px">
    <div class="song-cover" style="background:linear-gradient(135deg,#e8c060,#6a4a2a)" role="img" aria-label="Event poster artwork"></div>
    <span class="song-time">2:45m</span>
    <p class="song-title">Neque porro quisquam est qui dolorem ipsum</p>
    <p class="song-rating">Ratings <b>★★★★★</b></p>
    <div class="song-actions"><span class="dl">Download Now</span><span class="rate">Rate It Now</span></div>
  </div>
  <div class="song-card" style="left:768px;top:305px">
    <div class="song-cover" style="background:linear-gradient(135deg,#f0d040,#d03070 55%,#2a8ad0)" role="img" aria-label="Colourful concert poster artwork"></div>
    <span class="song-time">2:45m</span>
    <p class="song-title">Neque porro quisquam est qui dolorem ipsum</p>
    <p class="song-rating">Ratings <b>★★★★★</b></p>
    <div class="song-actions"><span class="dl">Download Now</span><span class="rate">Rate It Now</span></div>
  </div>

  <div class="dots" style="top:466px"><i class="on"></i><i></i><i></i><i></i></div>
</section>

<footer class="site-footer">
  <a class="footer-brand" href="#"><span class="brand-dot"></span><span class="brand-name">VeloraMusic</span></a>
  <nav class="footer-nav">
    <a href="#">Home</a><span>|</span><a href="#">About Us</a><span>|</span><a href="#">Artists</a><span>|</span><a href="#">Download Songs</a><span>|</span><a href="#">Contact Us</a>
  </nav>
  <div class="social"><i></i><i></i><i></i><i></i><i></i></div>
  <p class="legal">Terms Of Service | Privacy Policy</p>
</footer>

</body>
</html>
```